Wordpress Design Project for Bankruptcy Law Office in San Francisco

our current website: www.dorvanelilaw-example.com

we would like to re-design it for wordpress to make it faster and a bit more modern.

content should be similar to what we have there right now but also we do family law

please include logo for law office:

Law Office of Marta K. Dolvenidze

Thank you.
Updates

please see attached word document with logos that we like as an example.

we do tend to like color red.  darker red.

Please submit your design variations and logo as soon as possible.   We would like to go over them and make our decision

Reason: Please create couple of more variations of logo for your design, so we can make our decision what we like the most. Please see word doc for samples: Text: Law Office Of Marta K. Dolvenidze

Reason: final touches

Target Market(s)

bankruptcy and family law clients

Industry/Entity Type

Family Law

Requirements
Must have
• see examples of law sites
http://promo.lexorbin-example.com/testimonials

- new logo: Law Office of Marta K. Dolvenidze
- client intake form
- blog
- contact us form

Nice to have
• - map
- red color
- on the front page a nice photo of SF or a happy family

```html
<!DOCTYPE html>
<html lang="en">
<head>
<meta charset="utf-8">
<title>Law Office of Marta K. Dolvenidze</title>
<link href="https://fonts.googleapis.com/css2?family=Cinzel:wght@400&family=Oswald:wght@400&family=PT+Sans:wght@400;700&family=Arvo:wght@700&display=swap" rel="stylesheet">
<style>
:root{
  --bg:#ececec;
  --red-dark:#4b0606;
  --red-head:#b01f22;
  --red-box:#9a1518;
  --red-card:#d5101c;
  --red-title:#b01a1f;
  --ink:#222;
  --white:#fff;
  --yellow:#ffe400;
  --field:#dcdcdc;
}
*{margin:0;padding:0;box-sizing:border-box}
html,body{width:1096px;height:1200px;overflow:hidden;background:var(--bg)}
.stage{position:absolute;left:0;top:0;width:1200px;height:1314px;transform:scale(.91333);transform-origin:0 0;font-family:"PT Sans",sans-serif}
.page{position:absolute;left:115px;top:20px;width:970px;height:1267px;background:var(--white);box-shadow:0 0 12px rgba(0,0,0,.25)}
.abs{position:absolute}
.header{left:0;top:0;width:970px;height:108px;background:linear-gradient(180deg,#c22a2c,#9c1519)}
.header-photo{left:680px;top:0;width:290px;height:108px;background:linear-gradient(90deg,rgba(156,21,25,0),#7a2418 60%,#5e1a12)}
.logo-mark{left:13px;top:14px;width:103px;height:82px;background:#3a0404;border:1px solid #d9a0a0}
.logo-name{left:125px;top:16px;color:var(--white);font-family:"Cinzel",serif;font-weight:400;line-height:1}
.logo-name .small{display:block;font-size:27px;padding-left:108px}
.logo-name .big{display:block;font-size:36px;margin-top:4px;letter-spacing:1px}
.phone{left:768px;top:60px;display:flex;align-items:center;gap:8px;color:var(--white);font-family:"Cinzel",serif;font-size:27px}
.nav{left:0;top:108px;width:970px;height:44px;background:var(--red-dark)}
.nav a{position:absolute;top:11px;transform:translateX(-50%);color:var(--white);text-decoration:none;font-family:"Oswald",sans-serif;font-size:16px;letter-spacing:-.2px;white-space:nowrap}
.info-box{left:18px;top:174px;width:244px;height:278px;background:var(--red-box);color:var(--white)}
.info-box h3{position:absolute;left:16px;top:13px;font-weight:400;font-size:17px}
.info-box h4{position:absolute;left:16px;top:53px;font-weight:400;font-size:17px}
.info-photo{left:17px;top:78px;width:209px;height:83px;background:linear-gradient(135deg,#c9d9b0,#e9c9b8 50%,#cbb8d6);border:1px solid #fff}
.info-box p{position:absolute;left:19px;top:170px;width:204px;font-family:Arial,sans-serif;font-size:11px;line-height:15px;text-align:justify}
.clip{position:absolute}
.form-box{left:18px;top:474px;width:244px;height:336px;background:var(--red-box);border:2px dashed #c9c9c9;outline:1px solid #7a0c0e;color:var(--white)}
.form-box h3{position:absolute;left:14px;top:10px;font-size:17px;font-weight:700}
.form-box .req{position:absolute;left:22px;top:52px;font-size:13px}
.field{position:absolute;left:14px;width:205px;height:25px;background:linear-gradient(180deg,#f3f3f3,var(--field));border-radius:3px;color:#111;font-size:13px;padding:4px 8px}
.field.msg{height:70px}
.submit{position:absolute;left:152px;top:309px;width:66px;height:25px;background:#000;color:#fff;font-size:13px;text-align:center;line-height:25px;border-radius:3px 3px 0 0}
.hero{left:279px;top:174px;width:674px;height:278px;background:linear-gradient(90deg,#e8eef4 0%,#d6e2ec 45%,#c9d8e0 70%,#b9c9a8 100%)}
.hero-plant{left:290px;top:0;width:384px;height:278px;background:radial-gradient(ellipse at 55% 55%,#c9937e 0%,rgba(201,147,126,.6) 30%,rgba(201,147,126,0) 60%),linear-gradient(180deg,rgba(120,170,60,.35),rgba(120,170,60,0) 40%,rgba(150,170,160,.4))}
.hero-text{left:0;top:68px;width:300px;text-align:center;color:#161616;font-family:"Arvo",serif;font-weight:700}
.hero-text .l1{display:block;font-size:34px;letter-spacing:-.5px}
.hero-text .l2{display:block;font-size:25px;margin-top:6px}
.welcome{left:279px;top:472px;width:670px}
.welcome h1{color:var(--title,var(--red-title));font-size:19px;font-weight:700}
.welcome p{color:var(--ink);font-size:13.3px;line-height:22px;text-align:justify;margin:9px 0 0 3px}
.welcome p+p{margin-top:22px}
.welcome h2{color:var(--red-title);font-size:17px;font-weight:700;margin:20px 0 0 3px}
.welcome h2+p{margin-top:0}
.card{position:absolute;top:834px;width:298px;height:244px;background:linear-gradient(180deg,#e0121e,#c30a16);border-radius:6px;color:var(--white);box-shadow:0 8px 8px -4px rgba(0,0,0,.45)}
.card h3{position:absolute;left:23px;top:18px;font-size:28px;font-weight:400;white-space:nowrap}
.card-photo{position:absolute;left:22px;top:56px;width:251px;height:62px;background:linear-gradient(90deg,#e9e4de,#d8c4b2 40%,#cfc3b8 60%,#eef0f2)}
.card p{position:absolute;left:19px;top:124px;width:257px;font-family:Arial,sans-serif;font-size:12px;line-height:16px;text-align:justify}
.card .more{position:absolute;right:12px;top:216px;color:var(--yellow);font-family:Arial,sans-serif;font-size:12px;font-weight:700}
.footer{left:0;top:1123px;width:970px;height:144px;background:var(--red-dark);color:var(--white);font-family:Arial,sans-serif;font-size:12px}
.footer .top{position:absolute;left:22px;top:18px}
.footer .top span{margin-right:14px}
.footer .disc{position:absolute;left:22px;top:52px;width:670px;line-height:18px}
.badge-shadow{left:855px;top:38px;width:102px;height:82px;background:#7a3a3a}
.badge{left:844px;top:28px;width:103px;height:83px;background:var(--white)}
.badge i{position:absolute;left:8px;top:8px;width:32px;height:66px;background:#5a84c8}
</style>
</head>
<body>
<div class="stage">
  <div class="page">
    <header class="abs header">
      <div class="abs header-photo" role="img" aria-label="Photo of a judge's gavel resting on law books"></div>
      <div class="abs logo-mark"></div>
      <div class="abs logo-name"><span class="small">LAW OFFICE OF</span><span class="big">MARTA K. DOLVENIDZE</span></div>
      <div class="abs phone">
        <svg width="26" height="26" viewBox="0 0 26 26"><rect x="0" y="0" width="26" height="26" rx="4" fill="#e8e8e8"/><path d="M8 5c-2 1-3 3-2 6 2 5 5 8 10 10 3 1 5 0 6-2l-3-3-3 2c-2-1-5-4-6-6l2-3z" fill="#9c1519"/></svg>
        <span>415-555-0182</span>
      </div>
    </header>
    <nav class="abs nav">
      <a style="left:99px">HOME</a>
      <a style="left:217px">ABOUT US</a>
      <a style="left:369px">AREAS OF PRACTICE</a>
      <a style="left:525px">RESOURCES</a>
      <a style="left:642px">BLOG</a>
      <a style="left:733px">FAQ</a>
      <a style="left:840px">CONTACT US</a>
    </nav>

    <section class="abs info-box">
      <h3>IMPORTANT INFORMATION</h3>
      <h4>chapter 7</h4>
      <div class="abs info-photo" role="img" aria-label="Photo of a smiling family with children on bicycles"></div>
      <p>Often called the liquidation chapter, or "fresh start," chapter 7 is used by individuals, families, partnerships, or corporations whose financial difficulties do not allow them to repay all of their debts.</p>
    </section>
    <svg class="clip" style="left:236px;top:158px" width="14" height="44" viewBox="0 0 14 44"><rect x="2" y="2" width="10" height="40" rx="5" fill="none" stroke="#8a1013" stroke-width="2"/><rect x="5" y="8" width="4" height="28" rx="2" fill="none" stroke="#8a1013" stroke-width="1.5"/></svg>

    <section class="abs form-box">
      <h3>CONTACT FORM</h3>
      <div class="req">Fields marked with * are required.</div>
      <div class="field" style="top:83px">Name *</div>
      <div class="field" style="top:120px">Email *</div>
      <div class="field" style="top:156px">Phone</div>
      <div class="field" style="top:192px">Subject *</div>
      <div class="field msg" style="top:227px">Message *</div>
      <div class="submit">SUBMIT</div>
    </section>

    <section class="abs hero">
      <div class="abs hero-plant" role="img" aria-label="Photo of an open hand holding a small bonsai tree against a blue sky"></div>
      <svg class="abs" style="left:0;top:70px" width="300" height="130" viewBox="0 0 300 130">
        <g stroke="#8a8a8a" stroke-width="1"><line x1="0" y1="10" x2="132" y2="10"/><line x1="162" y1="10" x2="300" y2="10"/><line x1="0" y1="120" x2="132" y2="120"/><line x1="162" y1="120" x2="300" y2="120"/></g>
        <g fill="#8a8a8a"><polygon points="147,1 150,8 157,8 151,12 153,19 147,15 141,19 143,12 137,8 144,8"/><polygon points="147,111 150,118 157,118 151,122 153,129 147,125 141,129 143,122 137,118 144,118"/></g>
      </svg>
      <div class="abs hero-text"><span class="l1">Always Protecting</span><span class="l2">CLIENT'S INTERESTS!</span></div>
    </section>

    <section class="abs welcome">
      <h1>Welcome to Ledger Law 411 - Complete Bankruptcy Information</h1>
      <p>Gravel_-_main_pageThe Law Offices of Marta K. Dolvenidze is a consumer law office dedicated to consumer protection and zealously defending the rights of our clients. We offer the big firm quality legal representation with a small firm individualized attention to each client.</p>
      <p>Our office offers services in: all types of consumer bankruptcy filings, i.e. Chapter 7, Chapter 13, Chapter 11, negotiating a settlement of your debts, assisting you in the defense of collection litigation and defending you against foreclosure. Please review our site and see what we may be able to offer you. Feel free to call us at (415) 555-0182 or use our free case evaluation form.</p>
      <h2>Speak to a Lawyer</h2>
      <p>Unlike some other law firms, when you call the Law Office of Marta K. Dolvenidze you will speak to an actual attorney. Not a paralegal or assistant. And even after retaining our office you will still speak to an attorney unlike other firms where you cannot get a hold of your attorney after several attempts.</p>
    </section>

    <article class="card" style="left:19px">
      <h3>Debt Relief</h3>
      <div class="card-photo" role="img" aria-label="Photo of a relaxed smiling couple"></div>
      <p>This page is available, however, but because occasionally circumstances occur in which toil and pain can procure him some great. To take a trivial example, which of us ever undertakes laborious physical exercise, except to obtain some advantage from it.</p>
      <span class="more">read more...</span>
    </article>
    <article class="card" style="left:336px">
      <h3>Foreclosure Prevention</h3>
      <div class="card-photo" role="img" aria-label="Photo of a relaxed smiling couple"></div>
      <p>This page is available, however, but because occasionally circumstances occur in which toil and pain can procure him some great. To take a trivial example, which of us ever undertakes laborious physical exercise, except to obtain some advantage from it.</p>
      <span class="more">read more...</span>
    </article>
    <article class="card" style="left:652px">
      <h3>Chapter 13</h3>
      <div class="card-photo" role="img" aria-label="Photo of a relaxed smiling couple"></div>
      <p>This page is available, however, but because occasionally circumstances occur in which toil and pain can procure him some great. To take a trivial example, which of us ever undertakes laborious physical exercise, except to obtain some advantage from it.</p>
      <span class="more">read more...</span>
    </article>
    <svg class="clip" style="left:278px;top:818px" width="14" height="44" viewBox="0 0 14 44"><rect x="2" y="2" width="10" height="40" rx="5" fill="none" stroke="#9a9a9a" stroke-width="2"/><rect x="5" y="8" width="4" height="28" rx="2" fill="none" stroke="#9a9a9a" stroke-width="1.5"/></svg>
    <svg class="clip" style="left:598px;top:818px" width="14" height="44" viewBox="0 0 14 44"><rect x="2" y="2" width="10" height="40" rx="5" fill="none" stroke="#9a9a9a" stroke-width="2"/><rect x="5" y="8" width="4" height="28" rx="2" fill="none" stroke="#9a9a9a" stroke-width="1.5"/></svg>
    <svg class="clip" style="left:916px;top:818px" width="14" height="44" viewBox="0 0 14 44"><rect x="2" y="2" width="10" height="40" rx="5" fill="none" stroke="#9a9a9a" stroke-width="2"/><rect x="5" y="8" width="4" height="28" rx="2" fill="none" stroke="#9a9a9a" stroke-width="1.5"/></svg>

    <footer class="abs footer">
      <div class="top"><span>Go to top</span>Copyright © 2010 MKDLaw. All Rights Reserved. | Web Development by Webtidal | Design by LRN</div>
      <p class="disc">Disclaimer: The Law Offices of Marta K. Dolvenidze is a Debt Relief law firm as defined by 11 U.S.C. 528. We help people file for Bankruptcy Relief under the Bankruptcy Code. The information contained on this website is not to be construed as legal advice. It is not intended to solicit or form an attorney-client relationship. We do not guarantee any result and prior results do not guarantee a similar outcome. This is an attorney advertisement and this website is for informational purposes only.</p>
      <div class="abs badge-shadow"></div>
      <div class="abs badge"><i></i></div>
    </footer>
  </div>
</div>
</body>
</html>
```